Brightmoor Talent company

We require a website for job recruitment company called "Brightmoor Talent"
Our company is specialising in recruitment of skilled labour from Sri Lanka into Australian market.
We would like to include a job advertising plugin where jobs can be listed and applied for .
COPYWRITING MUST BE INCLUDED !

Industry/Entity Type

Recruitment

Coding

Coded - Design and coding required

Number of Pages Required

5+ page

Colors

Designer to choose colors to be used in the design.

```html
<!DOCTYPE html>
<html lang="en">
<head>
<meta charset="utf-8">
<title>Brightmoor Talent – Skilled Recruitment</title>
<link rel="stylesheet" href="https://fonts.googleapis.com/css2?family=Merriweather:wght@700;900&family=Roboto:wght@400;500;700&display=swap">
<style>
:root{
  --blue:#0b55a9;
  --blue-dark:#08428a;
  --blue-light:#8fb3de;
  --ink:#222;
  --muted:#555;
  --white:#fff;
  --line:#d9d9d9;
}
*{box-sizing:border-box;margin:0;padding:0}
html,body{width:1200px;height:5256px;overflow:hidden}
body{position:relative;background:var(--white);font-family:Roboto,Arial,sans-serif;color:var(--ink)}
.abs{position:absolute}
.serif{font-family:Merriweather,Georgia,serif}
.h2{font-family:Merriweather,Georgia,serif;font-weight:700;font-size:31px;color:var(--blue);text-align:center;letter-spacing:.5px;position:absolute;left:0;width:1200px}
.h2.light{color:var(--white)}
.brand{font-family:Merriweather,Georgia,serif;font-weight:900;color:var(--blue);display:flex;align-items:center;gap:10px}
.brand .mark{width:22px;height:22px;background:var(--blue)}

/* header */
.site-header{top:0;left:0;width:1200px;height:102px;background:var(--white)}
.site-header .brand{position:absolute;left:173px;top:34px;font-size:24px}
.btn-top{position:absolute;top:12px;height:38px;font-size:12px;font-weight:700;display:flex;align-items:center;justify-content:center;border-radius:4px}
.btn-outline{left:812px;width:120px;border:2px solid #333;color:#222}
.btn-solid{left:934px;width:94px;background:var(--blue);color:var(--white)}
.nav{position:absolute;top:64px;right:174px;display:flex;gap:30px;font-size:13px;font-weight:500;color:#222}

/* hero */
.hero{top:102px;left:0;width:1200px;height:1259px;background:var(--blue)}
.hero-photo{position:absolute;left:0;top:0;width:1200px;height:700px;background:linear-gradient(120deg,#5f6e80 0%,#c9d0d8 45%,#eef1f4 100%)}
.hero-wave{position:absolute;left:0;top:540px}
.hero-text{position:absolute;right:172px;top:140px;text-align:right}
.hero-text .brand{justify-content:flex-end;font-size:50px;line-height:1.1}
.hero-text .brand .mark{width:44px;height:44px}
.hero-text p{font-family:Merriweather,Georgia,serif;font-weight:700;font-size:28px;color:#111;line-height:1.35;margin-top:22px}
.hero-arrows{position:absolute;left:915px;top:420px}

.split{position:absolute;left:600px;top:694px;width:2px;height:460px;background:rgba(255,255,255,.85)}
.center-badge{position:absolute;left:526px;top:854px;width:148px;height:148px;border-radius:50%;background:var(--white);display:flex;align-items:center;justify-content:center;text-align:center;font-family:Merriweather,Georgia,serif;font-weight:900;color:var(--blue);font-size:17px;line-height:1.25}
.seek{position:absolute;width:340px;text-align:center;color:var(--white)}
.seek h3{font-family:Merriweather,Georgia,serif;font-size:21px;margin:28px 0 20px}
.seek p{font-size:12.5px;line-height:1.7}
.seek-left{left:160px;top:800px}
.seek-right{left:690px;top:800px}
.cta{position:absolute;left:367px;top:1154px;width:465px;height:44px;background:var(--white);border-radius:4px;font-size:13px;font-weight:700;color:#111;display:flex;align-items:center;justify-content:center}

/* process */
.process{top:1361px;left:0;width:1200px;height:693px}
.proc-label{position:absolute;font-family:Merriweather,Georgia,serif;font-weight:700;font-size:21px;color:var(--blue);line-height:1.2}
.node{position:absolute;width:72px;height:72px;border-radius:50%;background:var(--blue);border:4px solid var(--white);display:flex;align-items:center;justify-content:center}

/* industry */
.industry{top:2054px;left:0;width:1200px;height:376px;background:var(--blue)}
.ind{position:absolute;top:160px;width:180px;text-align:center;color:var(--white)}
.ind b{display:block;font-weight:500;font-size:16px;margin-top:22px;letter-spacing:.3px}
.ind span{display:block;font-size:13px;margin-top:8px}

/* jobs */
.job{position:absolute;left:173px;width:853px;height:135px;background:var(--white);border-radius:4px;box-shadow:0 2px 12px rgba(0,0,0,.22)}
.job .logo-box{position:absolute;top:10px;width:116px;height:116px;border:2px solid #333;border-radius:6px;display:flex;align-items:center;justify-content:center;gap:5px;font-weight:700;font-size:14px;color:#222}
.job .logo-box i{width:12px;height:12px;background:#222;display:block}
.job h4{position:absolute;top:22px;font-size:15px;font-weight:500;letter-spacing:.3px}
.job .meta{position:absolute;top:54px;font-size:13px;display:flex;gap:22px;align-items:center}
.job .meta span{display:flex;gap:6px;align-items:center}
.job p{position:absolute;top:80px;width:540px;font-size:11.5px;color:var(--muted);line-height:1.5}
.view{position:absolute;top:48px;width:104px;height:38px;border-radius:4px;font-family:Merriweather,Georgia,serif;font-weight:700;font-size:12px;display:flex;align-items:center;justify-content:center}
.view.out{border:2px solid var(--blue);color:var(--blue);background:var(--white)}
.view.fill{background:var(--blue);color:var(--white)}

/* why */
.why{top:3131px;left:0;width:1200px;height:525px}
.why-photo{position:absolute;left:0;top:0}
.why h2{position:absolute;left:680px;top:78px;font-family:Merriweather,Georgia,serif;font-size:31px;color:var(--blue)}
.acc{position:absolute;left:680px;width:346px;height:44px;border:2px solid #444;border-radius:4px;font-size:13px;font-weight:500;padding:0 14px;display:flex;justify-content:space-between;align-items:center;background:var(--white)}
.acc-body{position:absolute;left:680px;top:200px;width:346px;font-size:11.5px;color:var(--muted);line-height:1.75}
.why-badge{position:absolute;left:520px;top:180px;width:140px;height:140px;background:var(--white);border-radius:8px;display:flex;align-items:center;justify-content:center;text-align:center;font-family:Merriweather,Georgia,serif;font-weight:900;color:var(--blue);font-size:17px;line-height:1.25}

/* clients */
.clients{top:3656px;left:0;width:1200px;height:1210px}
.quote{position:absolute;top:206px;width:420px;height:334px;background:var(--white);box-shadow:0 2px 12px rgba(0,0,0,.2);text-align:center}
.avatar{width:106px;height:106px;border-radius:50%;margin:48px auto 0;background:radial-gradient(circle at 50% 40%,#8b7b70,#3a3330);border:3px solid var(--white);box-shadow:0 0 0 2px #333}
.quote p{font-size:12.5px;color:var(--muted);line-height:1.6;padding:0 22px;margin-top:26px}
.quote b{display:block;font-family:Merriweather,Georgia,serif;font-size:14px;color:var(--blue);margin-top:14px}

.post{position:absolute;top:724px;width:274px;height:394px;background:var(--white);box-shadow:0 2px 10px rgba(0,0,0,.2);text-align:center}
.post .img{height:196px;background:linear-gradient(135deg,#cfd4da,#7d8794 60%,#3f4754)}
.post h3{font-family:Merriweather,Georgia,serif;font-size:19px;color:#111;margin-top:20px}
.post p{font-size:12.5px;color:var(--muted);line-height:1.55;padding:0 20px;margin-top:12px}
.post .read{display:inline-flex;align-items:center;justify-content:center;width:104px;height:40px;background:var(--blue);color:var(--white);font-family:Merriweather,Georgia,serif;font-weight:700;font-size:12px;margin-top:16px;border-radius:3px}

/* footer */
.site-footer{top:4866px;left:0;width:1200px;height:390px}
.site-footer .brand{position:absolute;left:173px;top:132px;font-size:34px}
.site-footer .brand .mark{width:26px;height:26px}
.fcol{position:absolute;top:70px}
.fcol h5{font-family:Merriweather,Georgia,serif;font-size:19px;color:#111;margin-bottom:16px}
.fcol .rp{font-size:12.5px;font-weight:700;line-height:1.35;width:200px}
.fcol .rp small{display:block;font-weight:400;margin:6px 0 12px}
.fcol ul{list-style:none;font-size:12.5px;line-height:2}
.ct{display:flex;gap:12px;font-size:12.5px;font-weight:500;margin-bottom:14px;align-items:flex-start;line-height:1.4}
.ct i{flex:0 0 28px;height:28px;border-radius:50%;background:var(--blue);display:flex;align-items:center;justify-content:center}
.copy{position:absolute;left:0;top:326px;width:1200px;height:64px;background:var(--blue);color:var(--white);font-size:13px;font-weight:500;display:flex;align-items:center;justify-content:center}
</style>
</head>
<body>

<header class="site-header abs">
  <div class="brand"><span class="mark"></span>Brightmoor Talent</div>
  <div class="btn-top btn-outline">BROWSE JOBS</div>
  <div class="btn-top btn-solid">POST A JOB</div>
  <nav class="nav"><span>HOME</span><span>ABOUT</span><span>BLOG</span><span>SERVICES</span><span>BLOG</span><span>CONTACT</span></nav>
</header>

<section class="hero abs">
  <div class="hero-photo" role="img" aria-label="Two businessmen shaking hands in a bright office meeting room"></div>
  <svg class="hero-wave" width="1200" height="200" viewBox="0 0 1200 200"><path d="M0 130 C300 240 560 150 800 60 C960 0 1100 -10 1200 10 L1200 200 L0 200Z" fill="var(--blue)"/></svg>
  <div class="hero-text">
    <div class="brand"><span class="mark"></span>Brightmoor<br>Talent</div>
    <p>Find the Most Exciting<br>Jobs here...</p>
  </div>
  <svg class="hero-arrows" width="110" height="80" viewBox="0 0 110 80" fill="none" stroke="#333" stroke-width="3"><path d="M40 5 L8 40 L40 75"/><path d="M70 5 L102 40 L70 75"/></svg>

  <div class="split"></div>
  <div class="center-badge">Brightmoor<br>Talent</div>

  <div class="seek seek-left">
    <svg width="110" height="100" viewBox="0 0 110 100" fill="none" stroke="#fff" stroke-width="4"><rect x="8" y="22" width="80" height="58" rx="6"/><path d="M34 22 V10 H62 V22"/><path d="M8 44 H88"/><circle cx="78" cy="70" r="14" fill="var(--blue)"/><path d="M88 80 L102 94"/></svg>
    <h3>LOOKING FOR A JOB?</h3>
    <p>Our ability to match the right employee with the right employer has helped many candidates in making life changing move to Australia and to become PERMAN ENT RESIDENT of Australia.</p>
  </div>
  <div class="seek seek-right">
    <svg width="130" height="100" viewBox="0 0 130 100" fill="none" stroke="#fff" stroke-width="4"><circle cx="48" cy="32" r="20"/><circle cx="82" cy="32" r="20"/><path d="M14 96 C14 66 34 58 48 58 C62 58 82 66 82 96"/><path d="M50 96 C50 66 70 58 82 58 C96 58 116 66 116 96"/></svg>
    <h3>LOOKING FOR EMPLOYEES?</h3>
    <p>We know, how difficult it is to get the skilled labour force to help with business growth and expansion . That is why we search, screen and select only the best suitable candidates with all documents ready to apply for visa which will dramati cally save your time and money.</p>
  </div>
  <div class="cta">CALL US TODAY AND LET US HELP YOU EXPAND YOUR BUSINESS</div>
</section>

<section class="process abs">
  <h2 class="h2" style="top:70px">OUR JOB HIRING PROCESS</h2>
  <svg class="abs" style="left:416px;top:170px" width="368" height="368" viewBox="0 0 368 368">
    <circle cx="184" cy="184" r="182" fill="none" stroke="var(--blue)" stroke-width="3"/>
    <circle cx="184" cy="184" r="143" fill="var(--blue-light)"/>
    <circle cx="184" cy="184" r="130" fill="var(--white)"/>
    <circle cx="184" cy="184" r="122" fill="var(--blue)"/>
    <text x="184" y="176" text-anchor="middle" font-family="Merriweather,Georgia,serif" font-weight="900" font-size="26" fill="#fff">Brightmoor</text>
    <text x="184" y="210" text-anchor="middle" font-family="Merriweather,Georgia,serif" font-weight="900" font-size="26" fill="#fff">Talent</text>
  </svg>
  <div class="node" style="left:396px;top:242px"><svg width="34" height="30" viewBox="0 0 34 30" fill="none" stroke="#fff" stroke-width="2.5"><path d="M4 10 H12 L26 3 V27 L12 20 H4Z"/><path d="M29 11 L33 9 M29 19 L33 21"/></svg></div>
  <div class="node" style="left:732px;top:242px"><svg width="34" height="34" viewBox="0 0 34 34" fill="none" stroke="#fff" stroke-width="2.5"><circle cx="17" cy="17" r="14"/><text x="17" y="21" text-anchor="middle" font-size="10" font-weight="700" fill="#fff" stroke="none" font-family="Roboto,Arial,sans-serif">JOB</text></svg></div>
  <div class="node" style="left:400px;top:403px"><svg width="30" height="34" viewBox="0 0 30 34" fill="none" stroke="#fff" stroke-width="2.5"><rect x="3" y="3" width="22" height="28" rx="2"/><path d="M8 11 H20 M8 17 H20 M8 23 H16"/></svg></div>
  <div class="node" style="left:724px;top:403px"><svg width="32" height="34" viewBox="0 0 32 34" fill="none" stroke="#fff" stroke-width="2.5"><circle cx="16" cy="10" r="7"/><path d="M3 32 C3 22 10 19 16 19 C22 19 29 22 29 32"/></svg></div>
  <div class="node" style="left:564px;top:496px"><svg width="30" height="34" viewBox="0 0 30 34" fill="none" stroke="#fff" stroke-width="2.5"><rect x="3" y="5" width="22" height="27" rx="2"/><path d="M10 5 V2 H18 V5"/><path d="M9 19 L13 23 L20 14"/></svg></div>
  <div class="proc-label" style="right:812px;top:254px;text-align:right">ADVERTISE<br>FOR JOB</div>
  <div class="proc-label" style="left:823px;top:254px">ORGANISE JOB<br>INTERVIEWS</div>
  <div class="proc-label" style="right:812px;top:418px;text-align:right">COLLECTING<br>APPLICATIONS</div>
  <div class="proc-label" style="left:812px;top:418px">SHORTLIST<br>CANDIDATES</div>
  <div class="proc-label" style="left:0;width:1200px;top:580px;text-align:center">REVIEWING THE<br>SUITABLE CANDIDATES</div>
</section>

<section class="industry abs">
  <h2 class="h2 light" style="top:68px">JOBS BY INDUSTRY</h2>
  <div class="ind" style="left:141px"><svg width="72" height="72" viewBox="0 0 72 72" fill="none" stroke="#fff" stroke-width="3"><rect x="6" y="8" width="40" height="54" rx="3"/><path d="M14 30 V22 M22 30 V18 M30 30 V24"/><rect x="32" y="34" width="34" height="34" rx="3"/><path d="M38 42 H60 M38 50 H46 M52 50 H60 M38 58 H46 M52 58 H60"/></svg><b>ACCOUNTING</b><span>10 Positions</span></div>
  <div class="ind" style="left:328px"><svg width="72" height="72" viewBox="0 0 72 72" fill="none" stroke="#fff" stroke-width="3"><rect x="12" y="4" width="32" height="60" rx="4"/><path d="M24 56 H32"/><path d="M30 36 H40 L54 28 V54 L40 46 H30Z"/><path d="M60 34 L66 30 M60 42 H68 M60 50 L66 54"/></svg><b>DIGITAL</b><span>2 Postitions</span></div>
  <div class="ind" style="left:524px"><svg width="72" height="72" viewBox="0 0 72 72" fill="none" stroke="#fff" stroke-width="3"><path d="M6 24 L36 6 L66 24Z"/><path d="M8 24 H64 M14 30 V54 M26 30 V54 M46 30 V54 M58 30 V54 M6 56 H66 M4 64 H68"/></svg><b>BANKING</b><span>11 Postitions</span></div>
  <div class="ind" style="left:710px"><svg width="72" height="72" viewBox="0 0 72 72" fill="none" stroke="#fff" stroke-width="3"><circle cx="36" cy="14" r="9"/><path d="M14 46 L20 32 H52 L58 46"/><rect x="8" y="46" width="56" height="14" rx="4"/><circle cx="20" cy="64" r="4"/><circle cx="52" cy="64" r="4"/></svg><b>AUTOMOTIVE</b><span>20 Positions</span></div>
  <div class="ind" style="left:893px"><svg width="72" height="72" viewBox="0 0 72 72" fill="none" stroke="#fff" stroke-width="3"><rect x="6" y="12" width="60" height="40" rx="3"/><path d="M28 52 L24 64 H48 L44 52"/><path d="M30 40 L56 10 L62 16 L36 44 L28 46Z"/></svg><b>DESIGN</b><span>15 Positions</span></div>
</section>

<section>
  <h2 class="h2" style="top:2502px">RECENT JOBS</h2>
  <article class="job" style="top:2595px">
    <div class="logo-box" style="left:10px"><i></i>Kestrel Works</div>
    <h4 style="left:136px">SALES AND MARKETING COORDINATOR</h4>
    <div class="meta" style="left:136px"><span>&#9678; Australia</span><span>&#9673; Full Time</span></div>
    <p style="left:136px">Duis aute irure dolor in reprehenderit in voluptate velit esse cillum dolore eu fugiat nulla pariatur. Excepteur sint occaecat cupidatat non proident.</p>
    <div class="view out" style="right:22px">VIEW MORE</div>
  </article>
  <article class="job" style="top:2752px">
    <div class="view fill" style="left:20px">VIEW MORE</div>
    <h4 style="right:136px">CAR TRANSPORTER</h4>
    <div class="meta" style="right:136px"><span>Full Time &#9673;</span><span>Australia &#9678;</span></div>
    <p style="right:136px;text-align:right">Duis aute irure dolor in reprehenderit in voluptate velit esse cillum dolore eu fugiat nulla pariatur. Excepteur sint occaecat cupidatat non proident.</p>
    <div class="logo-box" style="right:10px"><i></i>Kestrel Works</div>
  </article>
  <article class="job" style="top:2917px">
    <div class="logo-box" style="left:10px"><i></i>Kestrel Works</div>
    <h4 style="left:136px">ELECTRONICS TECHNICIAN</h4>
    <div class="meta" style="left:136px"><span>&#9678; Australia</span><span>&#9673; Full Time</span></div>
    <p style="left:136px">Duis aute irure dolor in reprehenderit in voluptate velit esse cillum dolore eu fugiat nulla pariatur. Excepteur sint occaecat cupidatat non proident.</p>
    <div class="view out" style="right:22px">VIEW MORE</div>
  </article>
</section>

<section class="why abs">
  <svg class="why-photo" width="600" height="525" viewBox="0 0 600 525" role="img" aria-label="Businessman with glasses working at a laptop, tinted blue">
    <defs><linearGradient id="whyTone" x1="0" y1="0" x2="1" y2="1"><stop offset="0" stop-color="#3d6aa4"/><stop offset="1" stop-color="#0b55a9"/></linearGradient></defs>
    <path d="M0 0 H540 C560 120 620 300 520 525 H0Z" fill="url(#whyTone)"/>
  </svg>
  <div class="why-badge">Brightmoor<br>Talent</div>
  <h2>WHY CHOOSE US</h2>
  <div class="acc" style="top:146px">Nemo enim ipsam voluptatem?<span>&#8212;</span></div>
  <p class="acc-body">Aliquam sapien est, mollis id mattis id, scelerisque sed dolor. Proin accumsan erat sem, id porta risus dignissim ac. Vestibulum nec sapien in lacus ornare nec nec justo.</p>
  <div class="acc" style="top:282px">Enim ad minima veniam?<span>+</span></div>
  <div class="acc" style="top:342px">Sed ut perspiciatis unde omnis?<span>+</span></div>
  <div class="acc" style="top:402px">Quis autem vel eum iure reprehenderit?<span>+</span></div>
</section>

<section class="clients abs">
  <svg class="abs" style="left:0;top:300px" width="1200" height="910" viewBox="0 0 1200 910"><path d="M0 100 C300 20 900 20 1200 100 V910 H0Z" fill="var(--blue)"/></svg>
  <h2 class="h2" style="top:88px">WORDS FROM OUR CLIENTS</h2>
  <div class="quote" style="left:173px">
    <div class="avatar" role="img" aria-label="Portrait of client Daniel Okafor"></div>
    <p>Nemo enim ipsam voluptatem quia voluptas sit aspernatur aut odit aut fugit, sed quia consequuntur magni dolores eos qui ratio ne voluptatem sequi nesciunt. Neque porro quisquam est, qui dolorem ipsum quia dolor sit amet, consectetur</p>
    <b>- Daniel Okafor</b>
  </div>
  <div class="quote" style="left:606px">
    <div class="avatar" role="img" aria-label="Portrait of client Marcus Hale"></div>
    <p>Nemo enim ipsam voluptatem quia voluptas sit aspernatur aut odit aut fugit, sed quia consequuntur magni dolores eos qui ratio ne voluptatem sequi nesciunt. Neque porro quisquam est, qui dolorem ipsum quia dolor sit amet, consectetur</p>
    <b>- Marcus Hale</b>
  </div>

  <h2 class="h2 light" style="top:624px">LATEST BLOG</h2>
  <article class="post" style="left:173px"><div class="img" role="img" aria-label="Business team shaking hands across a meeting table"></div><h3>NEMO ENIM IPSAM</h3><p>Sed ut perspiciatis unde omnis iste natus error sit voluptatem accusantium dolorem que laudantium, totam rem aperiam.</p><span class="read">READ MORE</span></article>
  <article class="post" style="left:461px"><div class="img" role="img" aria-label="Group of colleagues in an office meeting"></div><h3>NEMO ENIM IPSAM</h3><p>Sed ut perspiciatis unde omnis iste natus error sit voluptatem accusantium dolorem que laudantium, totam rem aperiam.</p><span class="read">READ MORE</span></article>
  <article class="post" style="left:751px"><div class="img" role="img" aria-label="Happy office team celebrating with thumbs up"></div><h3>NEMO ENIM IPSAM</h3><p>Sed ut perspiciatis unde omnis iste natus error sit voluptatem accusantium dolorem que laudantium, totam rem aperiam.</p><span class="read">READ MORE</span></article>
</section>

<footer class="site-footer abs">
  <div class="brand"><span class="mark"></span>Brightmoor Talent</div>
  <div class="fcol" style="left:428px">
    <h5>RECENT POSTS</h5>
    <div class="rp">Nemo enim ipsam voluptatem quia voluptas<small>June 15, 2019</small></div>
    <div class="rp">Nemo enim ipsam voluptatem quia voluptas<small>June 15, 2019</small></div>
    <div class="rp">Nemo enim ipsam voluptatem quia voluptas<small>June 15, 2019</small></div>
  </div>
  <div class="fcol" style="left:660px">
    <h5>QUICK LINKS</h5>
    <ul><li>Home</li><li>About</li><li>Blog</li><li>Services</li><li>Jobs</li><li>Contact</li></ul>
  </div>
  <div class="fcol" style="left:830px">
    <h5>CONTACT US</h5>
    <div class="ct"><i><svg width="12" height="16" viewBox="0 0 12 16"><path d="M6 0 C2.7 0 0 2.6 0 5.8 C0 10 6 16 6 16 S12 10 12 5.8 C12 2.6 9.3 0 6 0Z" fill="#fff"/><circle cx="6" cy="6" r="2.2" fill="var(--blue)"/></svg></i><span>14 Harbour Lane,<br>Geelong, VIC 3220</span></div>
    <div class="ct"><i><svg width="14" height="14" viewBox="0 0 14 14"><path d="M3 0 L5 4 L3.5 5.5 C4.5 7.5 6.5 9.5 8.5 10.5 L10 9 L14 11 L12.5 14 C6 13.5 0.5 8 0 1.5Z" fill="#fff"/></svg></i><span>(03) 5550 1182<br>(03) 5550 1196</span></div>
    <div class="ct"><i><svg width="14" height="11" viewBox="0 0 14 11" fill="none" stroke="#fff" stroke-width="1.6"><rect x="1" y="1" width="12" height="9"/><path d="M1 1 L7 6 L13 1"/></svg></i><span>Mail:<br>info@brightmoortalent.com</span></div>
  </div>
  <div class="copy">Copyrights @ 2022 Brightmoor Talent.</div>
</footer>

</body>
</html>
```